Vibrant, yet professional, stationery set and other designs required.

I need to source a fantastic designer for a new project as part of my company using a new logo designed via sketch harbor.

**UPDATE** I am not looking for just 'fine' design that will suffice. I am looking for something great.

We are a life assurance brokerage based in Dublin, Ireland and BrightRoost.ie is our new website aimed at providing services for young families in Ireland. We are hoping to be the 'Velro' level of service providers in this area and I am looking for the quality of design to reflect this :-) Hopefully that makes sense!

I have a preference for straight lines over curves and waves.

I need...

1. Business card
2. Letterhead
3. Banner (for printing - 76cm X 305cm)
4. Car branding for KORVA 9 (2014 sport model) I believe the templates are freely available online.

Target Market(s)

Parents in Ireland - Aged 27 to 50.

Industry/Entity Type

Financial Planning

Colors

Designer to choose colors to be used in the design.

Requirements
Must have
• All of the items listed in the description above. I like clean, bright, legible, vibrant and professional design.
Should not have
• No silly or 'cheap' looking designs. This is a professional company looking to provide a professional service.

```html
<!DOCTYPE html>
<html lang="en">
<head>
<meta charset="utf-8">
<title>BrightRoost.ie – Business Card</title>
<link href="https://fonts.googleapis.com/css2?family=Roboto:wght@400;500;700&display=swap" rel="stylesheet">
<style>
  :root {
    --backdrop: #cdcdcd;
    --brand-orange: #f0821a;
    --brand-green: #8cc43f;
    --brand-blue: #6cc5e3;
    --brand-grey: #7f8c90;
    --ink: #4a4f52;
    --rule: #8a8f92;
    --paper: #f7f7f6;
    --white: #ffffff;
  }
  * { box-sizing: border-box; margin: 0; padding: 0; }
  html, body {
    width: 1200px; height: 960px; overflow: hidden;
    background: var(--backdrop);
    font-family: "Roboto", Arial, sans-serif;
  }
  .canvas { position: relative; width: 1200px; height: 960px; }

  .card {
    position: absolute; left: 320px; width: 600px; height: 342px;
    box-shadow: 0 3px 6px rgba(0,0,0,0.25);
  }

  /* Front */
  .card--front { top: 107px; background: var(--brand-orange); }
  .card--front .wordmark {
    position: absolute; left: 0; right: 0; top: 138px;
    text-align: center; color: var(--white);
    font-weight: 700; font-size: 60px; letter-spacing: -1px;
  }

  /* Back */
  .card--back { top: 493px; background: var(--paper); overflow: hidden; }
  .card--back .wordmark {
    position: absolute; right: 34px; top: 46px;
    color: var(--brand-grey); font-weight: 700; font-size: 46px; letter-spacing: -1px;
    display: flex; align-items: center; gap: 10px;
  }
  .wordmark__dot {
    width: 16px; height: 16px; border-radius: 50%; background: var(--brand-orange);
  }

  .person { position: absolute; left: 30px; top: 166px; }
  .person__name { color: var(--brand-orange); font-weight: 700; font-size: 20px; }
  .person__role { color: var(--brand-grey); font-weight: 500; font-size: 14px; margin-top: 4px; letter-spacing: 0.3px; }

  .divider {
    position: absolute; left: 28px; right: 31px; top: 213px;
    height: 1px; background: var(--rule);
  }

  .contacts { position: absolute; left: 29px; top: 221px; list-style: none; }
  .contacts li {
    display: flex; align-items: center; gap: 8px;
    height: 19px; font-size: 14px; color: var(--ink);
  }
  .contacts svg { width: 14px; height: 14px; fill: var(--brand-orange); flex: none; }

  .address {
    position: absolute; right: 28px; top: 258px;
    text-align: right; font-size: 14px; line-height: 18px; color: var(--ink); font-style: normal;
  }

  .footer-bands { position: absolute; left: 0; bottom: 0; width: 600px; height: 34px; }
  .footer-url {
    position: absolute; right: 22px; bottom: 8px;
    color: var(--white); font-size: 13px; letter-spacing: 4.5px;
  }
</style>
</head>
<body>
<main class="canvas">

  <section class="card card--front" aria-label="Business card front">
    <div class="wordmark">BrightRoost.ie</div>
  </section>

  <section class="card card--back" aria-label="Business card back">
    <div class="wordmark"><span class="wordmark__dot"></span>BrightRoost.ie</div>

    <div class="person">
      <p class="person__name">AIDAN KERR</p>
      <p class="person__role">CEO/FOUNDER</p>
    </div>

    <div class="divider"></div>

    <ul class="contacts">
      <li>
        <svg viewBox="0 0 24 24" aria-hidden="true"><path d="M6.6 10.8a15.1 15.1 0 0 0 6.6 6.6l2.2-2.2c.3-.3.7-.4 1-.2 1.1.4 2.3.6 3.6.6.6 0 1 .4 1 1V20c0 .6-.4 1-1 1A17 17 0 0 1 3 4c0-.6.4-1 1-1h3.5c.6 0 1 .4 1 1 0 1.3.2 2.5.6 3.6.1.3 0 .7-.2 1z"/></svg>
        614 220 7381
      </li>
      <li>
        <svg viewBox="0 0 24 24" aria-hidden="true"><path d="M7 1h10a2 2 0 0 1 2 2v18a2 2 0 0 1-2 2H7a2 2 0 0 1-2-2V3a2 2 0 0 1 2-2zm0 3v14h10V4zm5 15.2a1.2 1.2 0 1 0 0 2.4 1.2 1.2 0 0 0 0-2.4z"/></svg>
        872 515 0946
      </li>
      <li>
        <svg viewBox="0 0 24 24" aria-hidden="true"><path d="M6 2h12v5H6zM3 8h18a2 2 0 0 1 2 2v7h-4v5H5v-5H1v-7a2 2 0 0 1 2-2zm4 8v4h10v-4z"/></svg>
        459 703 2168
      </li>
      <li>
        <svg viewBox="0 0 24 24" aria-hidden="true"><path d="M2 5h20v14H2zm2 2v.5l8 5 8-5V7z"/></svg>
        hello@brightroost.ie
      </li>
    </ul>

    <address class="address">42 Harrow Quay<br>Dublin 2, Ireland D02 X7K4</address>

    <svg class="footer-bands" viewBox="0 0 600 34" aria-hidden="true">
      <polygon points="0,20 115,20 105,34 0,34" fill="var(--brand-green)"/>
      <polygon points="119,20 248,20 238,34 109,34" fill="var(--brand-orange)"/>
      <polygon points="252,20 358,20 348,34 242,34" fill="var(--brand-blue)"/>
      <polygon points="368,10 600,10 600,34 346,34" fill="var(--brand-grey)"/>
    </svg>
    <span class="footer-url">www.brightroost.ie</span>
  </section>

</main>
</body>
</html>
```